Design a Job Application & CV

I need a design for upcoming job applications that includes a cv. It needs to look as elegant and modern as possible as the application will be send mainly to large corporations and strategy consultancies. I have attached an application that I like for your consideration. One of the more difficult requirements is that it needs to be editable in ms office word for mac/windows.
As stated only the design is part of this project. I will fill in my content later on.
Reason: Dear Designers,
I am going to increase the budget as well as extending the deadline. I am hoping that you can improve upon the design that I have provided in the brief. If you have questions please let me know.
Dear Designers,
Target Market(s)
Human Resources Managers, Senior Consultants and Executives of larger firms
Industry/Entity Type
Office
Requirements
Must have
- 4 Pages including( a cover page, a coverletter page, 2 pages cv)
It should be easy to edit and should be readable by word for mac, i.e. in the *.docx format.
Here is an example of what I like:
http://www.torvenmald.example/applicationexample.pdf
http://www.torvenmald.example/applicationExample.docx
colors that I like are blue, grey, black, white
Nice to have
- icons to indicate sections
Should not have
- invasive cliparts

```html
<!DOCTYPE html>
<html lang="en">
<head>
<meta charset="utf-8">
<title>Application – Cover Page</title>
<link rel="stylesheet" href="https://fonts.googleapis.com/css2?family=Advent+Pro:wght@300;400&family=Crimson+Text&display=swap">
<style>
  :root {
    --brand-blue: #1a99d5;
    --slate-grey: #6d6e70;
    --paper: #ffffff;
    --map-deep: #1b4f8c;
    --map-mid: #2f72b4;
    --map-bright: #5d9bd3;
    --map-light: #b9d5ee;
    --floor: #f3f7fb;
    --reflection: #aec4da;
  }
  html, body {
    margin: 0;
    padding: 0;
    overflow: hidden;
    background: var(--paper);
  }
  .cover {
    position: relative;
    width: 848px;
    height: 1200px;
    overflow: hidden;
    background: var(--paper);
  }
  .cover__bands {
    position: absolute;
    inset: 0;
  }
  .cover__title {
    position: absolute;
    left: 28px;
    top: 46px;
    margin: 0;
    font-family: "Advent Pro", sans-serif;
    font-weight: 300;
    font-size: 84px;
    line-height: 1;
    letter-spacing: 0.5px;
    color: var(--paper);
  }
  .cover__hero {
    position: absolute;
    left: 0;
    top: 195px;
    width: 848px;
    height: 655px;
    background:
      radial-gradient(ellipse 46% 22% at 50% 58%, rgba(255,255,255,0.85) 0%, rgba(255,255,255,0) 100%),
      linear-gradient(180deg,
        var(--map-deep) 0%,
        var(--map-mid) 20%,
        var(--map-bright) 40%,
        var(--map-light) 52%,
        var(--floor) 58%,
        var(--paper) 70%,
        var(--reflection) 88%,
        var(--floor) 100%);
  }
  .cover__job-title {
    position: absolute;
    left: 28px;
    top: 860px;
    margin: 0;
    font-family: "Advent Pro", sans-serif;
    font-weight: 400;
    font-size: 60px;
    line-height: 1;
    color: var(--paper);
  }
  .applicant {
    position: absolute;
    left: 28px;
    top: 996px;
    color: var(--paper);
  }
  .applicant__name {
    margin: 0 0 16px;
    font-family: "Advent Pro", sans-serif;
    font-weight: 400;
    font-size: 37px;
    letter-spacing: 1.5px;
    line-height: 1;
  }
  .applicant__contact {
    margin: 0;
    font-family: "Crimson Text", serif;
    font-size: 19px;
    line-height: 22.8px;
    font-style: normal;
  }
</style>
</head>
<body>
  <main class="cover">
    <svg class="cover__bands" width="848" height="1200" viewBox="0 0 848 1200" aria-hidden="true">
      <polygon points="0,0 495,0 468,188 0,188" fill="var(--slate-grey)"/>
      <polygon points="506,0 848,0 848,188 479,188" fill="var(--brand-blue)"/>
      <polygon points="0,852 631,852 621,929 0,929" fill="var(--brand-blue)"/>
      <polygon points="643,852 848,852 848,929 633,929" fill="var(--slate-grey)"/>
      <rect x="0" y="936" width="848" height="264" fill="var(--slate-grey)"/>
    </svg>

    <h1 class="cover__title">APPLICATION</h1>

    <div class="cover__hero" role="img" aria-label="Hero image area: business team silhouettes standing before a dotted world map with light rays, reflected on a white floor"></div>

    <p class="cover__job-title">Job Title - CEO</p>

    <section class="applicant">
      <h2 class="applicant__name">LORENA ASHTVIK</h2>
      <address class="applicant__contact">
        2746 Cedar Lane, Suite 12<br>
        Los Angeles, CA 90025, USA<br>
        Mobil: : +1 (310) 555 0147<br>
        E-Mail: : lorena@mailbox.example
      </address>
    </section>
  </main>
</body>
</html>
```